I have a basic design of a poster that I want to make look better. The poster is a list of continuing medical education rules.

HBCPR = Harlowe Board for Clinical Practice Review This text should be included. You might also want to include "CME". Please use all the existing elements in the file.

I want to sell this poster to CME offices around the US. The poster should be 24 by 36

Reason: I would like to see more designs. I have received less than ten.

Target Market(s)

CME professionals

Industry/Entity Type

Medical

Colors

Designer to choose colors to be used in the design.

Requirements
Must have
• All elements in the file provided. You can also spell out Harlowe Board for Clinical Practice Review.

```html
<!DOCTYPE html>
<html lang="en">
<head>
<meta charset="utf-8">
<title>HBCPR Accreditation Criteria</title>
<link href="https://fonts.googleapis.com/css2?family=Anton&family=Oswald:wght@400;500&family=Roboto+Condensed:wght@400;700&display=swap" rel="stylesheet">
<style>
  :root {
    --plum: #5f0b3c;
    --plum-deep: #520832;
    --mauve: #9a6585;
    --card: #e1dfe0;
    --paper: #ffffff;
    --ink: #4a0a30;
  }
  * { box-sizing: border-box; margin: 0; padding: 0; }
  html, body { width: 800px; height: 1200px; overflow: hidden; background: var(--paper); }
  .poster { position: relative; width: 800px; height: 1200px; background: var(--paper); font-family: "Roboto Condensed", "Arial Narrow", sans-serif; }

  .masthead { position: absolute; left: 0; top: 0; width: 800px; height: 265px; background: var(--plum); }
  .masthead__texture { position: absolute; right: 0; top: 0; width: 290px; height: 112px;
    background: linear-gradient(225deg, rgba(175,130,160,.85) 0%, rgba(154,101,133,.55) 45%, rgba(95,11,60,0) 100%); }
  .masthead__title { position: absolute; left: 24px; top: 18px; font-family: "Anton", "Oswald", sans-serif; font-size: 58px; line-height: 1; color: #fff; letter-spacing: .5px; transform: scaleX(.86); transform-origin: left; white-space: nowrap; }
  .masthead__banner { position: absolute; left: 212px; top: 139px; width: 376px; height: 38px; background: #fff; border: 2px solid var(--plum-deep); outline: 2px solid #fff;
    font-family: "Oswald", sans-serif; font-size: 27px; color: var(--plum); text-align: center; line-height: 34px; letter-spacing: .5px; }
  .masthead__intro { position: absolute; left: 22px; right: 22px; top: 189px; color: #fff; font-size: 14.2px; line-height: 1.3; text-align: justify; }

  .criteria { position: absolute; left: 21px; top: 280px; width: 760px; display: grid; grid-template-columns: repeat(3, 240px); column-gap: 20px; row-gap: 18px; }
  .criterion { height: 122px; background: var(--card); padding: 12px 10px 8px; display: flex; flex-direction: column; align-items: center; }
  .criterion__label { background: var(--plum); color: #fff; font-family: "Oswald", sans-serif; font-weight: 500; font-size: 15.5px; padding: 1px 14px; margin-bottom: 8px; }
  .criterion__text { color: var(--ink); font-size: 11.6px; line-height: 1.28; text-align: justify; text-align-last: center; flex: 1; display: flex; align-items: center; }

  .commendation-band { position: absolute; left: 0; top: 974px; width: 800px; height: 48px; background: var(--plum); color: #fff; font-family: "Oswald", sans-serif; font-weight: 500; font-size: 27px; text-align: center; line-height: 48px; letter-spacing: .5px; }
  .commendation { position: absolute; left: 22px; top: 1030px; width: 756px; display: grid; grid-template-columns: repeat(7, 100px); column-gap: 9px; }
  .commendation .criterion { height: 118px; padding: 7px 6px; }
  .commendation .criterion__label { font-size: 11px; padding: 1px 8px; margin-bottom: 6px; }
  .commendation .criterion__text { font-size: 8.4px; line-height: 1.25; align-items: flex-start; }

  .footer { position: absolute; left: 0; bottom: 0; width: 800px; height: 42px; background: var(--plum); color: #fff; font-family: "Oswald", sans-serif; font-weight: 500; font-size: 18px; text-align: center; line-height: 42px; letter-spacing: .5px; }
</style>
</head>
<body>
<main class="poster">
  <header class="masthead">
    <div class="masthead__texture" role="img" aria-label="Decorative grid of mauve squares"></div>
    <h1 class="masthead__title">HBCPR ACCREDITATION CRITERIA</h1>
    <h2 class="masthead__banner">ACCREDITATION CRITERIA</h2>
    <p class="masthead__intro">The Accreditation Criteria are divided into three levels. To achieve Provisional Accreditation, a two year term, providers must comply with Criteria 1, 2, 3, and 7-12. Providers seeking full Accreditation or reaccreditation for a four-year term must comply with Criteria 1 -1 3.To achieve Accreditation with Commendation, a six-year term, providers must comply with all Accreditation Criteria tt</p>
  </header>

  <section class="criteria">
    <article class="criterion"><h3 class="criterion__label">Criterion 1</h3><p class="criterion__text">The provider has a CME mission statement that includes expected results articulated in terms of changes in competence, performance, or patient outcomes that will be the result of the program.</p></article>
    <article class="criterion"><h3 class="criterion__label">Criterion 2</h3><p class="criterion__text">The provider incorporates into CME activities the educational needs (knowledge, competence, or performance) that underlie the professional practice gaps of their own learners.</p></article>
    <article class="criterion"><h3 class="criterion__label">Criterion 3</h3><p class="criterion__text">The provider generates activities/educational interventions that are designed to change competence, performance, or patient outcomes as described in its mission statement.</p></article>
    <article class="criterion"><h3 class="criterion__label">Criterion 4</h3><p class="criterion__text">This criterion has been eliminated effective February 2014.</p></article>
    <article class="criterion"><h3 class="criterion__label">Criterion 5</h3><p class="criterion__text">The provider chooses educational formats for activities/interventions that are appropriate for the setting, objectives, and desired results of the activity.</p></article>
    <article class="criterion"><h3 class="criterion__label">Criterion 6</h3><p class="criterion__text">The provider develops activities/ educational interventions in the context of desirable physician attributes [eg, National Academy of Clinical Science (NACS) competencies, Graduate Clinical Training Council (GCTC) Competencies].</p></article>
    <article class="criterion"><h3 class="criterion__label">Criterion 7</h3><p class="criterion__text">The provider develops activities/educational interventions independent of commercial interests. (SCS 1, 2, and 6).</p></article>
    <article class="criterion"><h3 class="criterion__label">Criterion 8</h3><p class="criterion__text">The provider appropriately manages commercial support (if applicable, SCS 3 of the HBCPR Standards for Commercial Support).</p></article>
    <article class="criterion"><h3 class="criterion__label">Criterion 9</h3><p class="criterion__text">The provider maintains a separation of promotion from education (SCS 4).</p></article>
    <article class="criterion"><h3 class="criterion__label">Criterion 10</h3><p class="criterion__text">The provider actively promotes improvements in health care and NOT proprietary interests of a commercial interest (SCS 5).</p></article>
    <article class="criterion"><h3 class="criterion__label">Criterion 11</h3><p class="criterion__text">The provider analyzes changes in learners (competence, performance, or patient outcomes) achieved as a result of the overall program's activities/educational interventions.</p></article>
    <article class="criterion"><h3 class="criterion__label">Criterion 12</h3><p class="criterion__text">The provider gathers data or information and conducts a program-based analysis on the degree to which the CME mission of the provider has been met through the conduct of CME activities/educational interventions.</p></article>
    <article class="criterion"><h3 class="criterion__label">Criterion 13</h3><p class="criterion__text">The provider identifies, plans and implements the needed or desired changes in the overall program (eg, planners, teachers, infrastructure, methods, resources, facilities, interventions) that are required to improve on ability to meet the CME mission.</p></article>
    <article class="criterion"><h3 class="criterion__label">Criterion 14</h3><p class="criterion__text">This criterion has been eliminated effective February 2014.</p></article>
    <article class="criterion"><h3 class="criterion__label">Criterion 15</h3><p class="criterion__text">This criterion has been eliminated effective February 2014.</p></article>
  </section>

  <h2 class="commendation-band">ACCREDITATION WITH COMMENDATION</h2>

  <section class="commendation criteria--small">
    <article class="criterion"><h3 class="criterion__label">Criterion 16</h3><p class="criterion__text">The provider operates in a manner that integrates CME into the process for improving professional practice.</p></article>
    <article class="criterion"><h3 class="criterion__label">Criterion 17</h3><p class="criterion__text">The provider utilizes non-education strategies to enhance change as an adjunct to its activities/educational interventions (e.g., reminders, patient feedback).</p></article>
    <article class="criterion"><h3 class="criterion__label">Criterion 18</h3><p class="criterion__text">The provider identifies factors outside the provider's control that impact on patient outcomes.</p></article>
    <article class="criterion"><h3 class="criterion__label">Criterion 19</h3><p class="criterion__text">The provider implements educational strategies to remove, overcome or address barriers to physician change.</p></article>
    <article class="criterion"><h3 class="criterion__label">Criterion 20</h3><p class="criterion__text">The provider builds bridges with other stakeholders through collaboration and cooperation.</p></article>
    <article class="criterion"><h3 class="criterion__label">Criterion 21</h3><p class="criterion__text">The provider participates within an institutional or system framework for quality improvement.</p></article>
    <article class="criterion"><h3 class="criterion__label">Criterion 22</h3><p class="criterion__text">The provider is positioned to influence the scope and content of activities/educational interventions.</p></article>
  </section>

  <footer class="footer">www.hbcpr.org</footer>
</main>
</body>
</html>
```